Life Coaching business needs a new flyer

We are an Australian business that specialises in Life Coaching, Career Coaching, Health and Wellness Coaching, Yoga and Pilates. We need a A4 double sided flyer that is full colour and folded to DL format. I have attached a couple of designs that I like and some pictures and would like the flyer to be bright yet stylish.

Industry/Entity Type

Life Coaching

```html
<!DOCTYPE html>
<html lang="en">
<head>
<meta charset="utf-8">
<title>Clearpath Coaching &amp; Meditation Studio – DL Flyer</title>
<link href="https://fonts.googleapis.com/css2?family=Noto+Serif:wght@400;700&family=Open+Sans:wght@400;600&display=swap" rel="stylesheet">
<style>
  :root{
    --blue:#1a8fd6;
    --blue-deep:#0b6cb5;
    --blue-light:#6cc0ee;
    --green:#5cb82e;
    --teal:#1b8fb5;
    --ink:#333b42;
    --paper:#ffffff;
    --paper-grey:#f1f2f2;
    --stage:#b9b9b9;
  }
  *{margin:0;padding:0;box-sizing:border-box}
  html,body{width:1034px;height:1200px;overflow:hidden;background:var(--stage)}
  body{position:relative;font-family:"Open Sans",Arial,sans-serif;color:var(--ink)}
  .sheet{position:absolute;left:37px;width:960px;height:560px;display:flex;box-shadow:0 6px 18px rgba(0,0,0,.25);background:var(--paper)}
  .sheet--outside{top:25px}
  .sheet--inside{top:615px}
  .panel{position:relative;width:320px;height:560px;overflow:hidden}
  .panel + .panel{border-left:1px solid rgba(0,0,0,.06)}
  .wave{position:absolute;left:0;bottom:0;width:320px}
  .heading{font-family:"Noto Serif",Georgia,serif;font-weight:700;color:var(--teal);line-height:1.15}
  .body-text{font-size:10.5px;line-height:1.45}
  .body-text p{margin-bottom:8px}
  .photo{position:absolute}
  .brand{font-family:"Noto Serif",Georgia,serif;font-weight:700;text-transform:uppercase;letter-spacing:.5px;display:flex;align-items:center;gap:8px}
  .brand__dot{width:14px;height:14px;border-radius:50%;flex:none}

  /* Outside: testimonials */
  .testimonials{background:var(--paper)}
  .testimonials .heading{position:absolute;left:28px;top:28px;font-size:19px}
  .testimonials .body-text{position:absolute;left:28px;top:62px;width:266px;font-size:10px}
  .testimonials .photo{left:90px;top:380px;width:210px;height:120px;border-radius:0 30px 0 0;background:linear-gradient(160deg,#7fb6dc 0%,#f3c98a 55%,#c0734a 100%)}

  /* Outside: intro and contact */
  .intro{background:var(--paper-grey)}
  .intro .body-text{position:absolute;left:30px;top:28px;width:260px;font-size:9.5px}
  .contact{position:absolute;left:30px;top:108px;width:262px;padding:10px 14px;border-radius:10px;background:linear-gradient(180deg,var(--blue-light),var(--blue));color:#fff;font-family:"Noto Serif",Georgia,serif}
  .contact h2{font-size:15px;font-weight:700;margin-bottom:4px}
  .contact p{font-size:10px;line-height:1.45}
  .intro .brand{position:absolute;left:0;right:0;top:215px;justify-content:center;color:var(--teal);font-size:21px;flex-direction:column;gap:10px;text-align:center}
  .intro .brand__dot{width:60px;height:60px;background:var(--green)}
  .intro .photo{left:22px;top:330px;width:276px;height:110px;border-radius:0 40px 0 0;background:linear-gradient(120deg,#3a2c25,#8a6a55 50%,#2a2320)}
  .offer{position:absolute;left:0;right:0;bottom:26px;text-align:center;color:#fff;font-family:"Noto Serif",Georgia,serif;font-weight:700;font-size:13px;line-height:1.35}

  /* Outside: cover */
  .cover{background:linear-gradient(180deg,var(--blue-deep) 0%,var(--blue) 20%,var(--blue-light) 40%)}
  .cover .brand{position:absolute;left:26px;top:34px;color:#fff;font-size:17px}
  .cover .brand__dot{background:#fff}
  .cover .photo{left:0;top:80px;width:320px;height:360px;background:linear-gradient(180deg,#9ccbe9 0%,#cfe3ee 40%,#6fa04a 78%,#6a3d8a 100%)}
  .cover-title{position:absolute;left:0;right:0;bottom:34px;text-align:center;color:#fff;font-family:"Noto Serif",Georgia,serif;font-size:20px;line-height:1.35}

  /* Inside: questions and mission */
  .mission{background:linear-gradient(180deg,#f4fbfd 0%,#cfeef4 40%,#9fdbe6 100%)}
  .questions{position:absolute;left:28px;top:24px;width:270px;font-size:11px;font-weight:600;line-height:1.4;color:#1d2a33}
  .questions li{list-style:none;margin-bottom:6px}
  .mission .heading{position:absolute;left:28px;top:190px;font-size:17px;width:270px}
  .mission .body-text{position:absolute;left:28px;top:240px;width:268px}
  .mission .photo{left:80px;top:400px;width:170px;height:120px;background:linear-gradient(180deg,#6e8fa6,#2f3a44);border-radius:6px}

  /* Inside: coaching services */
  .services{background:linear-gradient(180deg,#ffffff 0%,#f3f6f8 100%)}
  .services .content{position:absolute;left:28px;top:22px;width:266px}
  .services .heading,.help .heading{font-size:16px;margin-bottom:4px}
  .services .body-text{margin-bottom:10px}

  /* Inside: why help */
  .help{background:linear-gradient(180deg,#ffffff 0%,#f4f0f4 100%)}
  .help .content{position:absolute;left:28px;top:22px;width:266px}
  .ticks{list-style:none;font-size:10px;font-style:italic;line-height:1.45;margin:4px 0 10px}
  .ticks li{display:flex;align-items:center;gap:6px}
  .ticks svg{flex:none}
  .help .brand{position:absolute;left:40px;top:440px;color:var(--teal);font-size:16px}
  .help .brand__dot{width:34px;height:34px;background:var(--green)}
</style>
</head>
<body>

<section class="sheet sheet--outside">

  <article class="panel testimonials">
    <h2 class="heading">Happy Clients Testimonials</h2>
    <div class="body-text">
      <p>“I have lost 10 kilos and now have the energy to play with my kids. Thanks Anna for your support, guidance and helping me get rid of my limiting beliefs. I feel I can achieve anything now! The sky's the limit” Mia, Mosman</p>
      <p>“I had always wanted to start up own café however every time it came to putting it into practice I would procrastinate and not achieve anything. I became overwhelmed with the whole process and never achieved anything. Anna put it into bite sized chunks and helped me to set small achievable goals. I am now a happy café owner.” Rosa, Double Bay</p>
      <p>“Anna has helped to change my life around in all aspects, I would have been lost without her. Thanks Anna for your professionalism, support and guidance.” Clare, Cremorne</p>
      <p>“I was so busy with kids, work, and my husband I lost who I was. Anna has helped me find the person I am again.” Helen, Chatswood</p>
    </div>
    <div class="photo" role="img" aria-label="Photo of a group of happy friends cheering at sunset"></div>
    <svg class="wave" viewBox="0 0 320 80" height="80" aria-hidden="true">
      <path d="M0 30 Q160 0 320 22 V80 H0Z" fill="var(--blue)"/>
      <path d="M0 30 Q160 0 320 22" fill="none" stroke="var(--green)" stroke-width="4"/>
      <path d="M0 38 Q160 10 320 30" fill="none" stroke="#fff" stroke-width="2" opacity=".7"/>
    </svg>
  </article>

  <article class="panel intro">
    <div class="body-text">
      <p>Clearpath Coaching &amp; Meditation Studio is a professional service that can help you achieve the goals that you are looking for in Life Coaching, Meditation, and Yoga/Pilates.</p>
      <p>If you are ready to take your life to the next level and would like to know more, please</p>
    </div>
    <div class="contact">
      <h2>contact us.</h2>
      <p>Phone : 02 9000 1234<br>hello@clearpathcoaching.com.au<br>www.clearpathcoaching.com.au</p>
    </div>
    <div class="brand"><span class="brand__dot"></span>Clearpath Coaching</div>
    <div class="photo" role="img" aria-label="Portrait photo of the two coaches"></div>
    <svg class="wave" viewBox="0 0 320 130" height="130" aria-hidden="true">
      <path d="M0 30 Q180 10 320 0 V130 H0Z" fill="var(--blue)"/>
      <path d="M0 30 Q180 10 320 0" fill="none" stroke="var(--green)" stroke-width="5"/>
    </svg>
    <p class="offer">Free Introductory Life Coaching<br>Phone/Video call session - 20 mins<br>(To see if coaching is right for you)</p>
  </article>

  <article class="panel cover">
    <div class="brand"><span class="brand__dot"></span>Clearpath Coaching</div>
    <div class="photo" role="img" aria-label="Photo of a woman meditating cross-legged on grass by the water"></div>
    <svg class="wave" viewBox="0 0 320 140" height="140" aria-hidden="true">
      <path d="M0 14 Q170 40 320 0 V140 H0Z" fill="var(--blue)"/>
      <path d="M0 14 Q170 40 320 0" fill="none" stroke="var(--green)" stroke-width="5"/>
    </svg>
    <p class="cover-title">Life Coaching<br>Meditation · Yoga/Pilates</p>
  </article>
</section>

<section class="sheet sheet--inside">

  <article class="panel mission">
    <ul class="questions">
      <li>Are you looking at making changes this year?</li>
      <li>Are you stuck in a rut or at a crossroad in your life?</li>
      <li>Are you wanting to lose weight but can't get motivated?</li>
      <li>Do you have ongoing problems with your career, relationships, or just life itself?</li>
      <li>Life coaching is the answer</li>
    </ul>
    <h2 class="heading">Clearpath Coaching &amp; Meditation Studio</h2>
    <div class="body-text">
      <p>Our mission is to help you become the best possible person you can be. Mentally, physically, and spiritually.</p>
      <p>We offer highly qualified and compassionate trainers/coaches for Life Coaching, Meditation, Yoga and Pilates.</p>
      <p>They will guide and motivate you every step of the way to achieve all your dreams and goals.</p>
      <p>They will make you be the best you can be</p>
    </div>
    <div class="photo" role="img" aria-label="Signpost pointing to life, balance, family, career, health and friends"></div>
    <svg class="wave" viewBox="0 0 320 40" height="40" aria-hidden="true">
      <path d="M0 40 L320 10 V40Z" fill="var(--blue)"/>
      <path d="M0 40 L320 10" fill="none" stroke="var(--green)" stroke-width="4"/>
    </svg>
  </article>

  <article class="panel services">
    <div class="content">
      <h2 class="heading">Life Coaching</h2>
      <div class="body-text">
        <p>Your Life Coach will give you the confidence and the ability to move forward in a positive manner in all areas of your life where you crave change.</p>
        <p>Life Coaching is about breaking down the barriers preventing this change from happening, and creating the ideal environment for positive action to take place. It is a holistic approach, which looks at the present and sets goals for a totally successful future.</p>
      </div>
      <h2 class="heading">Career Coaching</h2>
      <div class="body-text">
        <p>Are you at a crossroads in your career and at a loss about what to do next? Do you want your work to be in alignment with the authentic you? It can be difficult to assess career options, goals, and strategies, and have the confidence to implement changes on your own. With the right coaching support, you will gain the clarity that you need to take control and have a fulfilling and rewarding career.</p>
      </div>
      <h2 class="heading">Wellness Coaching</h2>
      <div class="body-text">
        <p>Health and wellness coaches help their clients find the motivation and tools to achieve their health and wellness goals, working with the client to examine and improve the psychological framework that supports those goals.</p>
      </div>
    </div>
    <svg class="wave" viewBox="0 0 320 40" height="40" aria-hidden="true">
      <path d="M0 10 Q160 30 320 20 V40 H0Z" fill="var(--blue)"/>
      <path d="M0 10 Q160 30 320 20" fill="none" stroke="var(--green)" stroke-width="4"/>
    </svg>
  </article>

  <article class="panel help">
    <div class="content">
      <h2 class="heading">Why Would I Need Help?</h2>
      <div class="body-text"><p>Coaching is for anyone who wants to make lasting changes in their life. Coaching can assist with such issues as:</p></div>
      <ul class="ticks">
        <li><svg width="12" height="10" viewBox="0 0 12 10"><path d="M1 5 L4.5 8.5 L11 1" fill="none" stroke="var(--green)" stroke-width="2"/></svg>Creating a better work-life balance</li>
        <li><svg width="12" height="10" viewBox="0 0 12 10"><path d="M1 5 L4.5 8.5 L11 1" fill="none" stroke="var(--green)" stroke-width="2"/></svg>Resolving relationship issues</li>
        <li><svg width="12" height="10" viewBox="0 0 12 10"><path d="M1 5 L4.5 8.5 L11 1" fill="none" stroke="var(--green)" stroke-width="2"/></svg>Career guidance</li>
        <li><svg width="12" height="10" viewBox="0 0 12 10"><path d="M1 5 L4.5 8.5 L11 1" fill="none" stroke="var(--green)" stroke-width="2"/></svg>Stress management</li>
        <li><svg width="12" height="10" viewBox="0 0 12 10"><path d="M1 5 L4.5 8.5 L11 1" fill="none" stroke="var(--green)" stroke-width="2"/></svg>Weight loss and fitness</li>
        <li><svg width="12" height="10" viewBox="0 0 12 10"><path d="M1 5 L4.5 8.5 L11 1" fill="none" stroke="var(--green)" stroke-width="2"/></svg>Motivation and goal setting</li>
        <li><svg width="12" height="10" viewBox="0 0 12 10"><path d="M1 5 L4.5 8.5 L11 1" fill="none" stroke="var(--green)" stroke-width="2"/></svg>Boosting your self esteem</li>
        <li><svg width="12" height="10" viewBox="0 0 12 10"><path d="M1 5 L4.5 8.5 L11 1" fill="none" stroke="var(--green)" stroke-width="2"/></svg>Overcoming negative emotions &amp; thoughts</li>
        <li><svg width="12" height="10" viewBox="0 0 12 10"><path d="M1 5 L4.5 8.5 L11 1" fill="none" stroke="var(--green)" stroke-width="2"/></svg>Better time management</li>
      </ul>
      <h2 class="heading">Meditation</h2>
      <div class="body-text"><p>We specialise in teaching meditation from beginners to advanced and teach a variety of techniques for stress reduction, peace of mind, stillness, and clarity.</p></div>
      <h2 class="heading">Yoga/Pilates</h2>
      <div class="body-text"><p>Your highly qualified and experienced Yoga or Pilates instructor will come to you and create a fun and varied workout based on what you enjoy and what your goals are.</p></div>
    </div>
    <div class="brand"><span class="brand__dot"></span>Clearpath Coaching</div>
    <svg class="wave" viewBox="0 0 320 70" height="70" aria-hidden="true">
      <path d="M0 20 Q160 40 320 0 V70 H0Z" fill="var(--blue)"/>
      <path d="M0 20 Q160 40 320 0" fill="none" stroke="var(--green)" stroke-width="4"/>
    </svg>
  </article>
</section>

</body>
</html>
```